Professional & attention grabbing.

A business card design, front and back. I already have a logo I will attach, but I am open to something new as well.
Things to include:
Name:
Title:
Phone:
Email:
Wanting something that is professional but attention grabbing.
Also we do a lot of work using drones on natural gas pipelines (leading the future)if you want to include any of that. I'm open to ideas.
Target Market(s)
Natural gas transmission industry / greenhouse gas mitigation industry
Industry/Entity Type
Business
Colors
Designer to choose colors to be used in the design.
Look and feel
Each slider illustrates characteristics of the customer's brand and the style your logo design should communicate.

```html
<!DOCTYPE html>
<html lang="en">
<head>
<meta charset="UTF-8">
<title>Veraline Inspections – Business Card</title>
<link rel="stylesheet" href="https://fonts.googleapis.com/css2?family=Exo+2:wght@400;500;700&display=swap">
<style>
  :root {
    --bg: #2b2b2d;
    --card-white: #ffffff;
    --brand-red: #c0202a;
    --ink-dark: #2f2f33;
    --ink-mid: #4a4a4f;
    --rule-red: #d8585e;
  }
  * { box-sizing: border-box; margin: 0; padding: 0; }
  html, body {
    width: 1200px; height: 900px; overflow: hidden;
    background: var(--bg);
    font-family: "Exo 2", sans-serif;
  }
  .stage {
    width: 1200px; height: 900px;
    display: flex; align-items: center; justify-content: center; gap: 48px;
  }
  .card {
    position: relative;
    width: 520px; height: 300px;
    border-radius: 22px;
    box-shadow: 0 14px 30px rgba(0,0,0,.35);
    overflow: hidden;
  }
  .card--front { background: var(--card-white); color: var(--ink-dark); }
  .card--back { background: var(--brand-red); color: #fff; }

  .wordmark {
    display: flex; align-items: center; gap: 10px;
    font-weight: 700; letter-spacing: .5px; text-transform: uppercase;
  }
  .wordmark__square { width: 26px; height: 26px; background: currentColor; }
  .card--front .wordmark {
    position: absolute; top: 52px; right: 36px;
    color: var(--ink-dark); font-size: 26px;
  }
  .card--front .wordmark__square { background: var(--brand-red); }

  .rule-top {
    position: absolute; top: 138px; left: 250px; right: 34px;
    height: 1px; background: var(--rule-red);
  }
  .address {
    position: absolute; top: 150px; right: 36px;
    text-align: right; font-size: 14px; line-height: 1.35; color: var(--ink-mid);
  }
  .person { position: absolute; left: 38px; top: 168px; }
  .person__name {
    font-size: 26px; font-weight: 700; color: var(--brand-red);
    text-transform: uppercase; letter-spacing: .5px; line-height: 1;
  }
  .person__title {
    margin-top: 6px; font-size: 15px; font-weight: 500;
    text-transform: uppercase; letter-spacing: 1px; color: var(--ink-mid);
  }
  .rule-contact {
    position: absolute; top: 224px; left: 38px; width: 210px;
    height: 1px; background: var(--rule-red);
  }
  .contact { position: absolute; left: 38px; top: 234px; list-style: none; }
  .contact__item {
    display: flex; align-items: center; gap: 9px;
    font-size: 15px; color: var(--ink-mid); line-height: 26px;
  }
  .contact__icon { width: 14px; height: 14px; flex: none; }

  .card--back .wordmark {
    position: absolute; top: 112px; left: 0; right: 0; justify-content: center;
    font-size: 34px; color: #fff;
  }
  .website {
    position: absolute; top: 196px; left: 0; right: 0;
    text-align: center; font-size: 14px; letter-spacing: .4px;
  }
</style>
</head>
<body>
<main class="stage">
  <section class="card card--front" aria-label="Business card front">
    <div class="wordmark"><span class="wordmark__square"></span>Veraline Inspections</div>
    <div class="rule-top"></div>
    <p class="address">418 Harlow Street,<br>Ashford Park, Tokyo</p>
    <div class="person">
      <h1 class="person__name">Daniel Reyes</h1>
      <p class="person__title">Director</p>
    </div>
    <div class="rule-contact"></div>
    <ul class="contact">
      <li class="contact__item">
        <svg class="contact__icon" viewBox="0 0 14 14"><rect width="14" height="14" rx="2" fill="#c0202a"/><path d="M4 3.5h2l.8 2-1.2.9a5 5 0 0 0 2 2l.9-1.2 2 .8v2A1 1 0 0 1 9.5 11 6.5 6.5 0 0 1 3 4.5a1 1 0 0 1 1-1z" fill="#fff"/></svg>
        555-014-2290
      </li>
      <li class="contact__item">
        <svg class="contact__icon" viewBox="0 0 14 14"><rect width="14" height="14" rx="2" fill="#c0202a"/><rect x="3" y="4" width="8" height="6" fill="none" stroke="#fff" stroke-width="1"/><path d="M3 4l4 3.2L11 4" fill="none" stroke="#fff" stroke-width="1"/></svg>
        hello@veraline.com
      </li>
    </ul>
  </section>

  <section class="card card--back" aria-label="Business card back">
    <div class="wordmark"><span class="wordmark__square"></span>Veraline Inspections</div>
    <p class="website">www.veraline.com</p>
  </section>
</main>
</body>
</html>
```